Vantiqo custom business card design

Need a authentic, innovative business card design for a new mobile app business. I am uploading a few screen images from our app for you to view. I would like app design theme to match business card design. I can also send logo images.

```html
<!DOCTYPE html>
<html lang="en">
<head>
<meta charset="utf-8">
<title>Vantiqo Business Card</title>
<link href="https://fonts.googleapis.com/css2?family=Open+Sans:wght@400;600;800&display=swap" rel="stylesheet">
<style>
  :root {
    --stage: #3a3b3d;
    --brand-purple: #5e0a8e;
    --ink: #1c1c1c;
    --paper: #ffffff;
    --text-grey: #333333;
    --rule: #8a8a8a;
    --url-light: #e9dff0;
  }
  * { margin: 0; padding: 0; box-sizing: border-box; }
  html, body { width: 1200px; height: 1000px; overflow: hidden; }
  body {
    background: var(--stage);
    font-family: "Open Sans", Arial, sans-serif;
    position: relative;
  }
  .card {
    position: absolute;
    width: 700px;
    height: 400px;
    left: 250px;
    overflow: hidden;
    box-shadow: 0 10px 28px rgba(0,0,0,.45);
  }
  /* Back side */
  .card-back { top: 50px; background: var(--brand-purple); }
  .card-back .back-wordmark {
    position: absolute; right: 40px; bottom: 78px;
    font-weight: 800; font-size: 54px; line-height: 1; color: var(--ink); letter-spacing: -1px;
  }
  .card-back .back-url {
    position: absolute; right: 42px; bottom: 46px;
    font-size: 17px; line-height: 1; color: var(--url-light); letter-spacing: 6px;
  }
  /* Front side */
  .card-front { top: 520px; background: var(--paper); }
  .band-purple {
    position: absolute; left: 0; top: 40px; width: 312px; height: 90px;
    background: var(--brand-purple);
  }
  .band-black {
    position: absolute; left: 312px; top: 80px; width: 388px; height: 118px;
    background: var(--ink);
  }
  .brand-dot {
    position: absolute; left: 254px; top: 80px; width: 116px; height: 116px;
    border-radius: 50%; background: var(--brand-purple); border: 3px solid var(--paper);
  }
  .front-wordmark {
    position: absolute; left: 162px; width: 300px; top: 206px; text-align: center;
    font-weight: 800; font-size: 46px; line-height: 1; color: var(--ink); letter-spacing: -1px;
  }
  .person {
    position: absolute; right: 345px; top: 270px; text-align: right;
    color: var(--text-grey); font-size: 17px; line-height: 22px;
  }
  .person .name { color: var(--brand-purple); font-weight: 600; font-size: 22px; line-height: 26px; }
  .person .role { text-transform: uppercase; margin-bottom: 4px; }
  .divider {
    position: absolute; left: 372px; top: 272px; width: 1px; height: 110px;
    background: linear-gradient(var(--rule), rgba(138,138,138,0));
  }
  .contacts {
    position: absolute; left: 392px; top: 270px; list-style: none;
    color: var(--text-grey); font-size: 17px; line-height: 23px;
  }
  .contacts li { display: flex; align-items: center; gap: 10px; }
  .contacts svg { width: 16px; height: 16px; fill: var(--brand-purple); flex: none; }
</style>
</head>
<body>

<section class="card card-back" aria-label="Business card back">
  <div class="back-wordmark">Vantiqo</div>
  <div class="back-url">www.vantiqo.com</div>
</section>

<section class="card card-front" aria-label="Business card front">
  <div class="band-purple"></div>
  <div class="band-black"></div>
  <div class="brand-dot"></div>
  <div class="front-wordmark">Vantiqo</div>

  <div class="person">
    <div class="name">MARK ELTON</div>
    <div class="role">President</div>
    <div>4127 Harbor Crest Lane</div>
    <div>Lakeview, OR 97630</div>
  </div>

  <div class="divider"></div>

  <ul class="contacts">
    <li><svg viewBox="0 0 16 16"><path d="M2 6c0-3 3-4 6-4s6 1 6 4l-3 1-1-2H6L5 7 2 6zM4 8h8l2 6H2l2-6zm4 1.5a2 2 0 100 4 2 2 0 000-4z"/></svg>555 0142 7781</li>
    <li><svg viewBox="0 0 16 16"><path d="M4 1h8v14H4V1zm1.5 2v9h5V3h-5zM8 12.8a.8.8 0 100 1.6.8.8 0 000-1.6z"/></svg>555 0198 3364</li>
    <li><svg viewBox="0 0 16 16"><path d="M4 1h7v4H4V1zM1 6h14v6h-2v3H3v-3H1V6zm3 4v3h8v-3H4z"/></svg>555 0176 2290</li>
    <li><svg viewBox="0 0 16 16"><path d="M1 3h14v10H1V3zm1.5 1.5L8 9l5.5-4.5H2.5z"/></svg>mark@vantiqo.com</li>
    <li><svg viewBox="0 0 16 16"><path d="M8 1a7 7 0 100 14A7 7 0 008 1zm0 1.5c.9 1 1.5 2.7 1.6 4.5H6.4C6.5 5.2 7.1 3.5 8 2.5zM6.4 8.5h3.2C9.5 10.3 8.9 12 8 13c-.9-1-1.5-2.7-1.6-4.5zM2.6 7a5.5 5.5 0 012.6-3.8C4.8 4.3 4.5 5.6 4.9 7H2.6zm0 1.5h2.3c0 1.4.3 2.7.8 3.8A5.5 5.5 0 012.6 8.5zm8.5 0h2.3a5.5 5.5 0 01-3.1 3.8c.5-1.1.8-2.4.8-3.8zm0-1.5c0-1.4-.3-2.7-.8-3.8A5.5 5.5 0 0113.4 7h-2.3z"/></svg>www.vantiqo.com</li>
  </ul>
</section>

</body>
</html>
```